Business card design for Morvane Engineering Tandem

We need a new business card design along with all the necessary to place an order. The company is Morvane Engineering Tandem and we recently updated our logo.

```html
<!DOCTYPE html>
<html lang="en">
<head>
<meta charset="utf-8">
<title>Morvane Engineering Tandem — Business Card</title>
<link rel="stylesheet" href="https://fonts.googleapis.com/css2?family=Montserrat:wght@400;500;700&display=swap">
<style>
  :root {
    --stage: #d9cdbd;
    --card: #ece4d8;
    --card-edge: #f6f1ea;
    --gold: #d4a11c;
    --ink: #2a2622;
    --ink-soft: #6a645b;
  }
  * { margin: 0; padding: 0; box-sizing: border-box; }
  html, body {
    width: 1200px;
    height: 1047px;
    overflow: hidden;
    background: var(--stage);
    font-family: "Montserrat", sans-serif;
  }
  .card {
    position: absolute;
    left: 151px;
    top: 289px;
    width: 948px;
    height: 518px;
    background: var(--card);
    border: 2px solid var(--card-edge);
    border-radius: 24px;
    box-shadow: 0 10px 40px rgba(80, 60, 30, 0.15);
  }
  .brand {
    position: absolute;
    left: 80px;
    top: 228px;
    display: flex;
    align-items: center;
    gap: 14px;
  }
  .brand-mark {
    width: 40px;
    height: 40px;
    background: var(--gold);
    flex: none;
  }
  .brand-name {
    font-weight: 700;
    font-size: 26px;
    line-height: 1.2;
    letter-spacing: 0.04em;
    color: var(--ink-soft);
    text-transform: uppercase;
  }
  .divider {
    position: absolute;
    left: 507px;
    top: 119px;
    width: 3px;
    height: 278px;
    background: var(--gold);
  }
  .details {
    position: absolute;
    left: 546px;
    top: 109px;
    color: var(--ink);
  }
  .person-name {
    font-weight: 700;
    font-size: 40px;
    letter-spacing: 0.02em;
    color: var(--gold);
    line-height: 44px;
  }
  .person-role {
    font-weight: 500;
    font-size: 25.5px;
    line-height: 30px;
    margin-top: 6px;
  }
  .address {
    font-weight: 500;
    font-size: 25.5px;
    line-height: 36px;
    margin-top: 20px;
  }
  .contacts {
    list-style: none;
    margin-top: 14px;
  }
  .contacts li {
    display: flex;
    align-items: center;
    gap: 11px;
    font-weight: 500;
    font-size: 25.5px;
    line-height: 36.5px;
  }
  .contacts svg {
    width: 19px;
    height: 19px;
    fill: var(--gold);
    flex: none;
  }
</style>
</head>
<body>
  <section class="card">
    <div class="brand">
      <span class="brand-mark"></span>
      <span class="brand-name">Morvane Engineering<br>Tandem</span>
    </div>

    <div class="divider"></div>

    <div class="details">
      <h1 class="person-name">OWEN CARTER</h1>
      <p class="person-role">Managing Director</p>
      <p class="address">Your address, City<br>State, Zip 1234</p>
      <ul class="contacts">
        <li>
          <svg viewBox="0 0 20 20" aria-hidden="true"><path d="M2 7c0-2 2-4 8-4s8 2 8 4v1h-4V6.5C13 6 7 6 6 6.5V8H2zM5 9h10l2 8H3z"/></svg>
          555 018 274
        </li>
        <li>
          <svg viewBox="0 0 20 20" aria-hidden="true"><path d="M2 4h16v2l-8 5-8-5zM2 8l8 5 8-5v8H2z"/></svg>
          info@youremail.com
        </li>
        <li>
          <svg viewBox="0 0 20 20" aria-hidden="true"><circle cx="10" cy="10" r="8"/><path d="M6 6c2 0 3 2 2 3s-2 2-1 4M13 4c-1 2 1 3 2 3M12 12c1 1 2 2 1 4" stroke="#ece4d8" stroke-width="1.4" fill="none"/></svg>
          www.yourwebsite.com
        </li>
      </ul>
    </div>
  </section>
</body>
</html>
```